Consulting Company PowerPoint Template Design

We are looking for an updated PowerPoint template design or our 55 person energy consulting firm (K7) based in San Francisco (www.kseven-example.com). We would like two versions of the same PowerPoint template in a 16:9 and 4:3 format with our existing logo.

We have an existing color scheme and template and are seeking your help to polish/update the template design for wide format and create a flexible template that is easy to use with content from Excel and Word. Our current template, and a couple of examples that we like are attached.

Specific requests include:

• Dark background for slide title
• A narrow section header
• Maximizing white space for content
• A limited number of well designed Master template layouts to choose from
• A selection of title and section header slides that are not San Francisco specific with some variety to chose from ideally with a focus on energy or nature, graphics/visuals.

For examples of energy specific templates see:
https://www.brightslidehub.example/energy/powerpoint-templates/0.html

Requirements
Must have
• Must use our logo but open to other designs, fonts, and styles for the PowerPoint template.
• Please use our existing color scheme found in the attached Excel file.
• Also we would like the ability to easily copy and paste from our existing/original template to the new template. In other words we would like backward compatibility to apply the new template format to our old PowerPoints that use our existing template.

```html
<!DOCTYPE html>
<html lang="en">
<head>
<meta charset="utf-8">
<title>K7 Slide – Bullet Levels</title>
<link href="https://fonts.googleapis.com/css2?family=Fira+Sans:wght@400;500;600&display=swap" rel="stylesheet">
<style>
  :root {
    --navy: #0d4c6a;
    --gold: #d4ab5e;
    --ink: #333a40;
    --white: #ffffff;
  }
  html, body { margin: 0; padding: 0; overflow: hidden; }
  body { width: 1200px; height: 900px; background: var(--white); font-family: "Fira Sans", Arial, sans-serif; color: var(--ink); }
  .slide { position: relative; width: 1200px; height: 900px; overflow: hidden; }

  .header-art { position: absolute; left: 0; top: 0; }
  .slide-title { position: absolute; left: 18px; top: 12px; margin: 0; font-size: 30px; font-weight: 500; color: var(--white); letter-spacing: 0.3px; }
  .slide-title .accent { color: var(--gold); }
  .brand-mark { position: absolute; left: 1116px; top: 0; width: 84px; height: 84px; display: flex; align-items: center; justify-content: center; font-size: 30px; font-weight: 600; color: var(--white); }

  .bullets { position: absolute; left: 0; top: 0; width: 1200px; }
  .item { position: absolute; margin: 0; line-height: 1.5; }
  .level-2 { left: 90px; width: 990px; font-size: 21px; }
  .level-2::before { content: ""; position: absolute; left: -46px; top: 4px; width: 24px; height: 24px; border-radius: 50%; background: var(--navy); box-shadow: 0 0 0 2px #9fb7c4; }
  .level-3 { left: 144px; font-size: 19.5px; }
  .level-3::before { content: ""; position: absolute; left: -26px; top: 8px; width: 16px; height: 16px; border-radius: 50%; background: var(--navy); }
  .level-4 { left: 198px; font-size: 19.5px; }
  .tick { position: absolute; left: -30px; top: 6px; }

  .footer-art { position: absolute; left: 0; top: 855px; }
  .footer-name { position: absolute; left: 9px; top: 860px; margin: 0; font-size: 24px; font-weight: 600; color: var(--white); }
  .page-number { position: absolute; left: 1138px; top: 864px; font-size: 19px; color: var(--white); }
</style>
</head>
<body>
<div class="slide">
  <svg class="header-art" width="1200" height="84" viewBox="0 0 1200 84" aria-hidden="true">
    <polygon points="0,0 1200,0 1200,66 1090,66 1082,75 0,75" fill="var(--gold)"/>
    <polygon points="0,0 1200,0 1200,66 1080,66 1080,66 0,66" fill="var(--navy)"/>
    <polygon points="0,66 1080,66 1090,75 0,75" fill="var(--gold)"/>
    <circle cx="1158" cy="42" r="41" fill="var(--white)"/>
    <circle cx="1158" cy="42" r="35" fill="var(--navy)"/>
  </svg>
  <h1 class="slide-title"><span class="accent">PROJECT</span> TITLE HERE</h1>
  <div class="brand-mark">K7</div>

  <div class="bullets">
    <p class="item level-2" style="top:142px">This page has more than four top-level bullets, so the second-level bullet format is used (just indent the first bullet)</p>
    <p class="item level-2" style="top:228px">Second level bullet (18 pt Verdana)</p>
    <p class="item level-2" style="top:281px">Second and subsequent level bullets use a “dot” bullet</p>
    <p class="item level-2" style="top:333px">The bullet color is Red 232; Green 95; Blue 49</p>
    <p class="item level-2" style="top:386px">Spacing and font sizing may be manually adjusted if necessary</p>
    <p class="item level-3" style="top:438px">Try first to edit the text to allow it to fit without changing spacing or size (3rd level = 16 pt)</p>
    <p class="item level-4" style="top:489px"><svg class="tick" width="22" height="20" viewBox="0 0 22 20" aria-hidden="true"><path d="M2 11 L8 17 L20 3" fill="none" stroke="var(--navy)" stroke-width="4"/></svg>This fosters readability and a consistent look (4th level = 14 pt)</p>
    <p class="item level-4" style="top:541px"><svg class="tick" width="22" height="20" viewBox="0 0 22 20" aria-hidden="true"><path d="M2 11 L8 17 L20 3" fill="none" stroke="var(--navy)" stroke-width="4"/></svg>Sometimes there is just too much to say and you will have to adjust</p>
  </div>

  <svg class="footer-art" width="1200" height="45" viewBox="0 0 1200 45" aria-hidden="true">
    <rect x="0" y="0" width="1200" height="45" fill="var(--navy)"/>
    <polygon points="1095,0 1200,0 1200,45 1110,45 1095,22" fill="var(--gold)"/>
  </svg>
  <p class="footer-name">Kinetic Seven Advisors</p>
  <span class="page-number">01</span>
</div>
</body>
</html>
```